BRIGHT RIVER POWER.

I'd like my business logo.
contact name: Dennis Halvorsen
phone:0438759164
email: info@brightriverpower.net.au
website: www.brightriverpower.net.au

services:
solar
battery storage
LED lighting
energy saving solutions
general electrical
I'd like the design to look professional

Target Market(s)

Everyone

Industry/Entity Type

Business

Contact Information for Business Card

as described above

Requirements
Must have
• Id like the colours and the design to work well with my logo.

```html
<!DOCTYPE html>
<html lang="en">
<head>
<meta charset="utf-8">
<title>Bright River Power — Business Card</title>
<link rel="stylesheet" href="https://fonts.googleapis.com/css2?family=Source+Sans+3:wght@400;600;700&display=swap">
<style>
  :root {
    --page-bg: #e9e6e2;
    --card-black: #050505;
    --brand-green: #7cc142;
    --brand-orange: #f7a81b;
    --contact-green: #8fd44a;
    --band-orange: #f9a61a;
    --band-text: #ffffff;
    --art-brown: rgba(92, 66, 18, 0.55);
    --art-green: rgba(47, 90, 30, 0.75);
  }
  * { box-sizing: border-box; margin: 0; padding: 0; }
  html, body {
    width: 1200px; height: 900px; overflow: hidden;
    background: var(--page-bg);
    font-family: "Source Sans 3", "Myriad Pro", Arial, sans-serif;
  }
  .business-card {
    position: absolute; left: 120px; top: 150px;
    width: 960px; height: 600px;
    background: var(--card-black);
    overflow: hidden;
    box-shadow: 0 10px 30px rgba(0,0,0,.25);
  }
  .brand-name {
    position: absolute; left: 60px; top: 110px;
    display: flex; align-items: center; gap: 16px;
    color: var(--brand-green);
    font-weight: 700; font-size: 42px; letter-spacing: .5px;
  }
  .brand-dot {
    width: 30px; height: 30px; border-radius: 50%;
    background: var(--brand-orange);
  }
  .hero-art {
    position: absolute; right: 0; top: 0;
    width: 440px; height: 496px;
    background: linear-gradient(160deg, transparent 15%, var(--art-brown) 55%, var(--art-green) 100%);
  }
  .contact-name {
    position: absolute; left: 75px; top: 282px;
    color: var(--brand-orange);
    font-weight: 600; font-size: 36px;
  }
  .contact-list {
    position: absolute; left: 75px; top: 350px;
    list-style: none;
  }
  .contact-item {
    display: flex; align-items: center; gap: 14px;
    height: 35px;
    color: var(--contact-green);
    font-size: 26px;
  }
  .contact-icon { width: 20px; height: 20px; fill: var(--brand-orange); }
  .accent-line {
    position: absolute; left: 0; top: 496px;
    width: 100%; height: 10px;
    background: var(--brand-green);
  }
  .services-band {
    position: absolute; left: 0; top: 506px;
    width: 100%; height: 94px;
    background: var(--band-orange);
    display: flex; align-items: center; justify-content: center;
    gap: 14px;
    color: var(--band-text); font-size: 22px;
    white-space: nowrap;
  }
  .service { display: flex; align-items: center; gap: 14px; }
  .service + .service::before {
    content: ""; width: 9px; height: 9px; border-radius: 50%;
    background: var(--band-text);
  }
</style>
</head>
<body>
  <main class="business-card">
    <div class="brand-name"><span class="brand-dot"></span>BRIGHT RIVER POWER</div>

    <div class="hero-art" role="img" aria-label="Large faint sun and leaf illustration in dark brown and green tones"></div>

    <h1 class="contact-name">Dennis Halvorsen</h1>

    <ul class="contact-list">
      <li class="contact-item">
        <svg class="contact-icon" viewBox="0 0 24 24" aria-hidden="true"><path d="M6.6 10.8a15.1 15.1 0 0 0 6.6 6.6l2.2-2.2c.3-.3.7-.4 1-.2 1.1.4 2.3.6 3.6.6.6 0 1 .4 1 1V20c0 .6-.4 1-1 1A17 17 0 0 1 3 4c0-.6.4-1 1-1h3.5c.6 0 1 .4 1 1 0 1.3.2 2.5.6 3.6.1.3 0 .7-.2 1z"/></svg>
        0438759164
      </li>
      <li class="contact-item">
        <svg class="contact-icon" viewBox="0 0 24 24" aria-hidden="true"><path d="M3 5h18v14H3z"/><path d="M3 5l9 7 9-7" fill="none" stroke="#050505" stroke-width="1.6"/></svg>
        info@brightriverpower.net.au
      </li>
      <li class="contact-item">
        <svg class="contact-icon" viewBox="0 0 24 24" aria-hidden="true"><circle cx="12" cy="12" r="10"/><path d="M2 12h20M12 2c3 3 3 17 0 20M12 2c-3 3-3 17 0 20" fill="none" stroke="#050505" stroke-width="1.6"/></svg>
        www.brightriverpower.net.au
      </li>
    </ul>

    <div class="accent-line"></div>

    <div class="services-band">
      <span class="service">Solar</span>
      <span class="service">Battery Storage</span>
      <span class="service">LED Lighting</span>
      <span class="service">Energy Saving Solutions</span>
      <span class="service">General Electrical</span>
    </div>
  </main>
</body>
</html>
```